Letterhead for a German Distribution/Manufacturing Company

We need a professional Letterhead in a unique Design.
not to playful.
The Letterhead has to show show that we are a international company with headquater in Germany.
all details like adress, Vat Tax Number, Bank Accout, Eori, email, Company number has to be on the Letterhead.
for example use: VAT TAX DE5470318 Bank Account: Kestrel Bank IBAN DE412058731ß204683 Swift: MORV0417352 EORI 3150428697 Company Number: HRB 51806 Adress: VOLMINTA UG Ahornweg 7 Postal Code 06384 City Kelmstadt Country: Germany Email: info@volminta-example.com
the design can be colored but doesnt have to be
Industry/Entity Type
Manufacturing and international distribution
Requirements
Must have
- show that we are a international company with headquater in Germany. our company infos and logo

```html
<!DOCTYPE html>
<html lang="en">
<head>
<meta charset="utf-8">
<title>VOLMINTA Letterhead</title>
<link rel="stylesheet" href="https://fonts.googleapis.com/css2?family=Lato:wght@400;700&family=Montserrat:wght@500&family=Dancing+Script:wght@500&display=swap">
<style>
  :root {
    --backdrop: #e4e4e4;
    --paper: #ffffff;
    --ink: #1f1f1f;
    --brand: #4a4a4a;
    --rule: #555555;
  }
  html, body {
    margin: 0;
    padding: 0;
    width: 1200px;
    height: 1200px;
    overflow: hidden;
    background: var(--backdrop);
    font-family: "Lato", Arial, sans-serif;
    color: var(--ink);
  }
  .letterhead {
    position: absolute;
    left: 200px;
    top: 20px;
    width: 800px;
    height: 1160px;
    background: var(--paper);
    box-shadow: 0 2px 10px rgba(0,0,0,0.12);
  }
  .brand {
    position: absolute;
    left: 47px;
    top: 62px;
    display: flex;
    align-items: center;
    gap: 14px;
  }
  .brand-mark {
    width: 48px;
    height: 48px;
    border-radius: 50%;
    background: var(--brand);
  }
  .brand-name {
    font-size: 48px;
    font-weight: 400;
    color: var(--brand);
    letter-spacing: 1px;
    line-height: 1;
  }
  .letter {
    position: absolute;
    left: 47px;
    top: 296px;
    width: 707px;
    font-size: 15px;
    line-height: 18.4px;
  }
  .letter p { margin: 0; }
  .date { margin-bottom: 21px !important; }
  .recipient { margin-bottom: 21px !important; }
  .salutation {
    font-size: 19px;
    font-weight: 700;
    line-height: 22px;
    margin: 30px 0 36px !important;
  }
  .recipient + .salutation { margin-top: 10px !important; }
  .body-text {
    text-align: justify;
    margin-bottom: 20px !important;
  }
  .closing { margin-top: 40px !important; }
  .signature {
    font-family: "Dancing Script", cursive;
    font-size: 36px;
    line-height: 1;
    margin-top: 34px !important;
  }
  .footer-rule {
    position: absolute;
    left: 47px;
    top: 982px;
    width: 707px;
    height: 3px;
    background: var(--rule);
  }
  .company-details {
    position: absolute;
    left: 47px;
    top: 1012px;
    width: 707px;
    text-align: center;
    font-family: "Montserrat", Arial, sans-serif;
    font-size: 12px;
    font-weight: 500;
    line-height: 20px;
  }
  .company-details p { margin: 0; }
</style>
</head>
<body>
  <main class="letterhead">
    <header class="brand">
      <span class="brand-mark"></span>
      <span class="brand-name">VOLMINTA</span>
    </header>

    <section class="letter">
      <p class="date">January-03-2020</p>
      <p class="recipient">Mr, Adam Crane<br>President</p>
      <p class="recipient">Harlow Group<br>45 Market Lane, Suite# 10<br>City, State, 120023</p>
      <p class="salutation">Dear Mr, Adam</p>
      <p class="body-text">Lorem ipsum dolor sit amet, consectetur adipisicing elit, sed do eiusmod tempor incididunt ut labore et dolore magna aliqua. Ut enim ad minim veniam, quis nostrud exercitation ullamco laboris nisi ut aliquip ex ea commodo consequat. Duis aute irure dolor in reprehenderit in voluptate velit esse cillum dolore eu fugiat nulla pariatur.</p>
      <p class="body-text">Lorem ipsum dolor sit amet, consectetur adipisicing elit, sed do eiusmod tempor incididunt ut labore et dolore magna aliqua. Ut enim ad minim veniam, quis nostrud exercitation ullamco laboris nisi ut aliquip ex ea commodo consequat. Duis aute irure dolor in reprehenderit in voluptate velit esse cillum dolore eu fugiat nulla pariatur.</p>
      <p class="body-text">Lorem ipsum dolor sit amet, consectetur adipisicing elit, sed do eiusmod tempor incididunt ut labore et dolore magna aliqua. Ut enim ad minim veniam, quis nostrud exercitation ullamco laboris nisi ut aliquip ex ea commodo consequat.</p>
      <p class="body-text">Excepteur sint occaecat cupidatat non proident, sunt in culpa qui officia deserunt mollit anim id est laborum. re et dolore magnam aliquam quaerat voluptatem.</p>
      <p class="closing">Regards</p>
      <p class="signature">Daniel Hart</p>
    </section>

    <div class="footer-rule"></div>
    <footer class="company-details">
      <p>VAT TAX DE5470318</p>
      <p>Bank Account: Kestrel Bank IBAN DE412058731ß204683 Swift: MORV0417352</p>
      <p>EORI 3150428697</p>
      <p>Company Number: HRB 51806</p>
      <p>Adress: VOLMINTA UG Ahornweg 7 Postal Code 06384 City Kelmstadt Country</p>
      <p>Germany Email: info@volminta-example.com</p>
    </footer>
  </main>
</body>
</html>
```